Business Cards for IT Consulting Company (Managed Service Provider)

I am looking to have some business cards printed and would like some designs. We are an IT Consulting company based in Vancouver BC. I would like a nice clean and modern look to the cards. I have uploaded all the versions of my logo so parts can be used as needed. Here is a snippit from our website homepage:

Quillbrook Networks Ltd. is an IT Solutions Partner located in Vancouver BC, Canada. We offer IT solutions and support to customers in the greater Vancouver Area. With expertise in Microsoft platforms, as well as Linux and Mac OSX and over 12 years experience in the IT industry, Quillbrook Networks is dedicated to offering our clients top quality service and products. We take pride in the solutions we offer our customers. The greatest compliment a client can give us is to recommend our services.

Quillbrook Networks Ltd. offers a wide range of IT services from onsite service to remote support and managed service solutions. This allows clients to choose the support path that best suits their company’s needs. Supporting many different sized companies from small to enterprise level over the past 12 years Quillbrook Networks has the experience and expertise needed to ensure things run smoothly. Allowing our clients to focus on doing business.

Revolutionizing the way IT services are delivered.

Quillbrook Networks is dedicated to providing our clients with IT solutions that work and grow with them for years to come. This philosophy helps save money in the long run instead of replacing equipment constantly. Far too often IT solutions are not well thought out and while possibly solving the problem at hand, require replacement due to growth or quality within a very short time frame. Quillbrook Networks takes pride in providing solutions that will last and be able to accommodate growth without the need for replacement.

Industry/Entity Type

Information Technology

Contact Information for Business Card

Quillbrook Networks Ltd.
(Employee Name)
Eml: (Employees Email Address)
Web: quillbrook.me
Ph: 604-555-0148

Font styles to use
Serif
Sans Serif

Requirements
Must have
• The Company logo and company colors.
Nice to have
• - Our tag line: "Revolutionizing IT Services" or "Revolutionizing the way IT services are delivered."
• - Also I really like the idea of nature and technology together blending which is sort of where my logo came from so integrating that somehow onto the business cards would be great.

```html
<!DOCTYPE html>
<html lang="en">
<head>
<meta charset="UTF-8">
<title>Quillbrook Networks Ltd. – Business Cards</title>
<link href="https://fonts.googleapis.com/css2?family=Montserrat:wght@400;600;700&family=Roboto:ital,wght@0,400;1,400&display=swap" rel="stylesheet">
<style>
  :root {
    --backdrop: #b1afaf;
    --card-dark: #1f1f20;
    --card-light: #f3f3f3;
    --brand-blue: #1a8fd6;
    --brand-grey: #58595b;
    --text-dark: #3f3f3f;
    --text-light: #e8e8e8;
  }
  * { box-sizing: border-box; margin: 0; padding: 0; }
  html, body {
    width: 1200px;
    height: 1200px;
    overflow: hidden;
    background: var(--backdrop);
  }
  .canvas { position: relative; width: 1200px; height: 1200px; }

  .card {
    position: absolute;
    width: 713px;
    height: 418px;
    overflow: hidden;
  }
  .card--front { left: 238px; top: 118px; background: var(--card-dark); }
  .card--back  { left: 231px; top: 644px; background: var(--card-light); }

  .brand {
    position: absolute;
    display: flex;
    align-items: center;
    gap: 16px;
  }
  .brand__dot {
    border-radius: 50%;
    background: var(--brand-blue);
    flex: none;
  }
  .brand__name {
    font-family: "Montserrat", sans-serif;
    font-weight: 600;
    color: var(--brand-blue);
    white-space: nowrap;
    letter-spacing: 0.2px;
  }
  .card--front .brand { left: 110px; top: 168px; }
  .card--front .brand__dot { width: 40px; height: 40px; }
  .card--front .brand__name { font-size: 35px; }

  .card--back .brand { left: 47px; top: 68px; }
  .card--back .brand__dot { width: 34px; height: 34px; }
  .card--back .brand__name { font-size: 30px; }

  .tagline {
    position: absolute;
    left: 0; right: 0;
    top: 377px;
    display: flex;
    justify-content: center;
    align-items: center;
    gap: 16px;
  }
  .tagline__rule {
    width: 110px;
    height: 3px;
    background: var(--brand-blue);
  }
  .tagline__text {
    font-family: "Montserrat", sans-serif;
    font-weight: 400;
    font-size: 18.5px;
    color: var(--text-light);
  }

  .person {
    position: absolute;
    left: 415px;
    top: 194px;
  }
  .person__name {
    font-family: "Montserrat", sans-serif;
    font-weight: 700;
    font-size: 24px;
    color: var(--brand-blue);
  }
  .person__title {
    font-family: "Roboto", sans-serif;
    font-style: italic;
    font-size: 16px;
    color: var(--text-dark);
    margin-top: 4px;
  }
  .contact {
    position: absolute;
    left: 416px;
    top: 274px;
    list-style: none;
  }
  .contact__item {
    display: flex;
    align-items: center;
    height: 27.5px;
    font-family: "Roboto", sans-serif;
    font-size: 18px;
    color: var(--text-dark);
  }
  .contact__icon {
    width: 18px;
    height: 18px;
    margin-right: 17px;
    fill: var(--brand-blue);
  }
  .footer-band {
    position: absolute;
    left: 0; bottom: 0;
    width: 713px;
    height: 22px;
  }
</style>
</head>
<body>
<main class="canvas">

  <section class="card card--front" aria-label="Card front">
    <div class="brand">
      <span class="brand__dot"></span>
      <span class="brand__name">Quillbrook Networks Ltd.</span>
    </div>
    <div class="tagline">
      <span class="tagline__rule"></span>
      <span class="tagline__text">Revolutionizing IT Services</span>
      <span class="tagline__rule"></span>
    </div>
  </section>

  <section class="card card--back" aria-label="Card back">
    <div class="brand">
      <span class="brand__dot"></span>
      <span class="brand__name">Quillbrook Networks Ltd.</span>
    </div>

    <div class="person">
      <p class="person__name">Daniel Hart</p>
      <p class="person__title">Managing Director</p>
    </div>

    <ul class="contact">
      <li class="contact__item">
        <svg class="contact__icon" viewBox="0 0 20 20" aria-hidden="true">
          <path d="M2 6c0-2 2-3 8-3s8 1 8 3v2h-4V6.5c-1-.5-7-.5-8 0V8H2z"/>
          <path d="M5 9h10l2 8H3z"/>
        </svg>
        604-555-0148
      </li>
      <li class="contact__item">
        <svg class="contact__icon" viewBox="0 0 20 20" aria-hidden="true">
          <circle cx="10" cy="10" r="8" fill="none" stroke="#1a8fd6" stroke-width="1.6"/>
          <ellipse cx="10" cy="10" rx="3.5" ry="8" fill="none" stroke="#1a8fd6" stroke-width="1.4"/>
          <path d="M2 10h16M3.5 6h13M3.5 14h13" stroke="#1a8fd6" stroke-width="1.3"/>
        </svg>
        www.quillbrook.me
      </li>
      <li class="contact__item">
        <svg class="contact__icon" viewBox="0 0 20 20" aria-hidden="true">
          <path d="M1 4h18v12H1z"/>
          <path d="M1 4l9 7 9-7" fill="none" stroke="#f3f3f3" stroke-width="1.5"/>
        </svg>
        support@quillbrook.me
      </li>
    </ul>

    <svg class="footer-band" viewBox="0 0 713 22" aria-hidden="true">
      <polygon points="478,2 713,2 713,22 458,22" fill="var(--brand-grey)"/>
      <polygon points="0,4 505,4 472,22 0,22" fill="var(--brand-blue)"/>
    </svg>
  </section>

</main>
</body>
</html>
```